Business Card For Halvenmoor Financial Consulting

Hi, I would like a business card designed. Bold, modern.
Please use the same design as the logo. I have also attached the website design to see the overall theme.
Wordmark Font
Color: Hex: #01AEF7

```html
<!DOCTYPE html>
<html lang="en">
<head>
<meta charset="utf-8">
<title>Halvenmoor Financial Consulting – Business Card</title>
<link rel="stylesheet" href="https://fonts.googleapis.com/css2?family=Jost:ital,wght@0,400;0,500;0,700;1,400&display=swap">
<style>
  :root {
    --page: #e4e5e7;
    --ink-dark: #18222b;
    --brand-blue: #01aef7;
    --band-blue: #34ade6;
    --white: #ffffff;
    --text-on-band: #14202a;
  }
  * { box-sizing: border-box; margin: 0; padding: 0; }
  html, body {
    width: 1200px; height: 800px; overflow: hidden;
    background: var(--page);
    font-family: "Jost", "Futura", sans-serif;
  }
  .sheet {
    width: 1200px; height: 800px;
    display: flex; align-items: center; justify-content: center; gap: 40px;
  }
  .card {
    position: relative;
    width: 560px; height: 320px;
    overflow: hidden;
    box-shadow: 0 10px 28px rgba(0,0,0,.18);
  }
  .card-bg { position: absolute; inset: 0; }

  .company-name {
    position: absolute;
    color: var(--white);
    font-weight: 700;
    line-height: 1.1;
    white-space: nowrap;
  }
  .front .company-name { left: 0; right: 0; top: 48px; text-align: center; font-size: 34px; }
  .back .company-name { right: 28px; top: 36px; text-align: right; font-size: 28px; }

  .front .web {
    position: absolute; left: 190px; right: 20px; top: 272px;
    text-align: center; color: var(--text-on-band);
    font-size: 15px; font-weight: 500; letter-spacing: 4.6px;
  }

  .contact-list {
    position: absolute; left: 28px; top: 118px;
    list-style: none; color: var(--white); font-size: 14px;
  }
  .contact-list li { display: flex; align-items: center; gap: 9px; height: 24px; }
  .contact-list svg { width: 13px; height: 13px; fill: var(--brand-blue); flex: none; }
  .address {
    position: absolute; left: 28px; top: 262px;
    color: var(--text-on-band); font-size: 15px;
  }
  .person {
    position: absolute; right: 28px; top: 200px;
    text-align: right; color: var(--text-on-band);
  }
  .person-name { font-size: 22px; font-weight: 700; letter-spacing: .5px; }
  .person-role { font-size: 14px; font-style: italic; }
</style>
</head>
<body>
<main class="sheet">

  <section class="card front" aria-label="Business card front">
    <svg class="card-bg" viewBox="0 0 560 320" aria-hidden="true">
      <rect width="560" height="320" fill="var(--band-blue)"/>
      <polygon points="0,0 560,0 560,240 172,240 152,138 0,138" fill="var(--ink-dark)"/>
      <polyline points="0,144 147,144 167,246 560,246" fill="none" stroke="var(--white)" stroke-width="2"/>
    </svg>
    <p class="company-name">Halvenmoor Consulting</p>
    <p class="web">www.halvenmoorconsulting.com</p>
  </section>

  <section class="card back" aria-label="Business card back">
    <svg class="card-bg" viewBox="0 0 560 320" aria-hidden="true">
      <rect width="560" height="320" fill="var(--band-blue)"/>
      <polygon points="0,0 560,0 560,172 395,172 330,228 0,228" fill="var(--ink-dark)"/>
      <polyline points="0,234 333,234 398,178 560,178" fill="none" stroke="var(--white)" stroke-width="2"/>
    </svg>
    <p class="company-name">Halvenmoor Consulting</p>
    <ul class="contact-list">
      <li>
        <svg viewBox="0 0 16 16" aria-hidden="true"><path d="M3 1h3l1.5 4-2 1.3a9 9 0 0 0 4.2 4.2L11 8.5l4 1.5v3a2 2 0 0 1-2 2A13 13 0 0 1 1 3a2 2 0 0 1 2-2z"/></svg>
        (025) 481 20375
      </li>
      <li>
        <svg viewBox="0 0 16 16" aria-hidden="true"><path d="M1 3h14v10H1zM2 4.2v.6l6 4 6-4v-.6z"/></svg>
        info@halvenmoor.co
      </li>
      <li>
        <svg viewBox="0 0 16 16" aria-hidden="true"><path d="M8 1a7 7 0 1 0 0 14A7 7 0 0 0 8 1zm0 1.5c.9 0 1.9 1.7 2.2 4.5H5.8C6.1 4.2 7.1 2.5 8 2.5zM2.6 8.5h2.2c.1 1.8.5 3.4 1.1 4.5a5.5 5.5 0 0 1-3.3-4.5zm0-1.5a5.5 5.5 0 0 1 3.3-4.5c-.6 1.1-1 2.7-1.1 4.5zm5.4 6.5c-.9 0-1.9-1.7-2.2-5h4.4c-.3 3.3-1.300 5-2.2 5zm2.1-.5c.6-1.1 1-2.7 1.1-4.5h2.2a5.5 5.5 0 0 1-3.3 4.5zm1.1-6c-.1-1.8-.5-3.4-1.1-4.5A5.5 5.5 0 0 1 13.4 7z"/></svg>
        www.halvenmoorconsulting.com
      </li>
    </ul>
    <p class="address">2218 Brackenridge Lane, Corvale, FL 32904</p>
    <div class="person">
      <p class="person-name">MARLA QUINT</p>
      <p class="person-role">Manager</p>
    </div>
  </section>

</main>
</body>
</html>
```